Business card design for Automotive workshop

We need a business card for a new automotive repair and tyre shop called Keelstone Prime Automotive located in New Zealand. We are a clean, modern and fresh workshop and company.

Front needs to feature logo,
my name:
Marlo Fenwicke (director)

Address:
48 Tarn Lane
Harrowmere 3592

Phone: 07 594 2713
Mobile: 027 451 9362
Email: office@keelstoneautomotive.example.nz
Website: keelstoneautomotive.example.nz

Back needs to feature an area to write down appointment details, date and time.

Also feature a list of jobs and work we do such as,
Vehicle Servicing
All Mechanical Repairs
Warrant of Fitness
Tyres & Wheel Alignments
Automotive Diagnostics
Automotive Parts & Supplies

```html
<!DOCTYPE html>
<html lang="en">
<head>
<meta charset="utf-8">
<title>Keelstone Prime Automotive – Business Card</title>
<link rel="stylesheet" href="https://fonts.googleapis.com/css2?family=Exo+2:ital,wght@0,400;0,600;0,700;1,400&family=Open+Sans:wght@400;600;700&display=swap">
<style>
  :root {
    --backdrop: #6b727c;
    --card-black: #0b0b0b;
    --card-white: #ffffff;
    --brand-red: #e3141e;
    --text-light: #f2f2f2;
    --rule-dots: #555555;
  }
  * { box-sizing: border-box; margin: 0; padding: 0; }
  html, body {
    width: 1200px; height: 900px; overflow: hidden;
    background: var(--backdrop);
    font-family: "Exo 2", sans-serif;
  }
  .canvas { position: relative; width: 1200px; height: 900px; }
  .card {
    position: absolute; left: 280px; width: 640px; height: 366px;
    overflow: hidden; box-shadow: 0 8px 24px rgba(0,0,0,.35);
  }

  /* ---------- Back side ---------- */
  .card-back { top: 50px; background: var(--card-black); }
  .back-texture {
    position: absolute; inset: 0;
    background: radial-gradient(ellipse at 45% 35%, #3a3a3a 0%, #1a1a1a 45%, #0b0b0b 80%);
  }
  .back-logo {
    position: absolute; left: 36px; top: 120px;
    color: var(--brand-red); font-weight: 700; text-transform: uppercase;
    line-height: 1.05;
  }
  .back-logo .logo-main { display: block; font-size: 30px; letter-spacing: 1px; }
  .back-logo .logo-sub { display: block; font-size: 14px; letter-spacing: 5px; }
  .services {
    position: absolute; left: 360px; top: 26px;
    font-family: "Open Sans", sans-serif; color: var(--text-light);
  }
  .services-title {
    color: var(--brand-red); font-weight: 700; font-size: 15px;
    letter-spacing: .5px; margin-bottom: 4px;
  }
  .services-list { list-style: none; font-size: 13.5px; line-height: 1.45; }
  .services-list li::before {
    content: "•"; color: var(--brand-red); margin-right: 8px; font-weight: 700;
  }
  .appointment {
    position: absolute; left: 80px; right: 0; top: 222px; bottom: 0;
    background: var(--card-white);
    padding: 30px 34px 0 34px;
    font-family: "Open Sans", sans-serif;
  }
  .appt-row { display: flex; align-items: baseline; gap: 8px; margin-bottom: 36px; }
  .appt-label { color: var(--brand-red); font-size: 15px; }
  .appt-line { flex: 1; border-bottom: 2px dotted var(--rule-dots); height: 1px; }

  /* ---------- Front side ---------- */
  .card-front { top: 480px; background: var(--card-white); }
  .front-logo {
    position: absolute; left: 0; right: 0; top: 58px; text-align: center;
    color: var(--brand-red); font-weight: 700; text-transform: uppercase;
    line-height: 1.05;
  }
  .front-logo .logo-main { display: block; font-size: 46px; letter-spacing: 2px; }
  .front-logo .logo-sub { display: block; font-size: 20px; letter-spacing: 9px; margin-top: 4px; }
  .front-band { position: absolute; inset: 0; }
  .person {
    position: absolute; left: 30px; top: 214px; color: var(--text-light);
  }
  .person-name { color: var(--brand-red); font-size: 27px; font-weight: 400; }
  .person-role { font-size: 15px; font-style: italic; margin-top: -2px; }
  .address { font-size: 16px; font-style: italic; margin-top: 14px; line-height: 1.3; }
  .contacts {
    position: absolute; right: 20px; bottom: 26px;
    list-style: none; color: var(--text-light); text-align: right;
  }
  .contacts li {
    display: flex; justify-content: flex-end; align-items: center; gap: 12px;
    line-height: 1.45;
  }
  .contacts .phone { font-size: 18px; letter-spacing: 1px; }
  .contacts .web { font-size: 14.5px; }
  .contacts svg { width: 15px; height: 15px; fill: var(--brand-red); flex: none; }
</style>
</head>
<body>
<main class="canvas">

  <section class="card card-back" aria-label="Card back">
    <div class="back-texture" role="img" aria-label="Dark hexagon mesh background texture"></div>
    <div class="back-logo">
      <span class="logo-main">Keelstone Prime</span>
      <span class="logo-sub">Automotive</span>
    </div>
    <div class="services">
      <p class="services-title">VEHICLE SERVICING</p>
      <ul class="services-list">
        <li>All Mechanical Repairs</li>
        <li>Warrant of Fitness</li>
        <li>Tyres &amp; Wheel Alignments</li>
        <li>Automotive Diagnostics</li>
        <li>Automotive Parts &amp; Supplies</li>
      </ul>
    </div>
    <div class="appointment">
      <div class="appt-row">
        <span class="appt-label">Date:</span><span class="appt-line"></span>
        <span class="appt-label">Time:</span><span class="appt-line"></span>
      </div>
      <div class="appt-row">
        <span class="appt-label">Date:</span><span class="appt-line"></span>
        <span class="appt-label">Time:</span><span class="appt-line"></span>
      </div>
    </div>
  </section>

  <section class="card card-front" aria-label="Card front">
    <svg class="front-band" viewBox="0 0 640 366" preserveAspectRatio="none" aria-hidden="true">
      <polyline points="0,180 84,180 106,200 130,188 640,188" fill="none" stroke="var(--brand-red)" stroke-width="4"/>
      <path d="M0 186 H82 L106 206 L132 194 H640 V366 H0 Z" fill="var(--card-black)"/>
    </svg>
    <div class="front-logo">
      <span class="logo-main">Keelstone Prime</span>
      <span class="logo-sub">Automotive</span>
    </div>
    <div class="person">
      <p class="person-name">Marlo Fenwicke</p>
      <p class="person-role">Director</p>
      <p class="address">48 Tarn Lane<br>Harrowmere 3592</p>
    </div>
    <ul class="contacts">
      <li class="phone">07 594 2713
        <svg viewBox="0 0 24 24" aria-label="Phone"><path d="M6.6 10.8a15.1 15.1 0 0 0 6.6 6.6l2.2-2.2a1 1 0 0 1 1-.25 11.4 11.4 0 0 0 3.6.57 1 1 0 0 1 1 1V20a1 1 0 0 1-1 1A17 17 0 0 1 3 4a1 1 0 0 1 1-1h3.5a1 1 0 0 1 1 1c0 1.25.2 2.45.57 3.57a1 1 0 0 1-.25 1z"/></svg></li>
      <li class="phone">027 451 9362
        <svg viewBox="0 0 24 24" aria-label="Mobile"><path d="M7 1h10a2 2 0 0 1 2 2v18a2 2 0 0 1-2 2H7a2 2 0 0 1-2-2V3a2 2 0 0 1 2-2zm0 3v15h10V4z"/></svg></li>
      <li class="web">office@keelstoneautomotive.example.nz
        <svg viewBox="0 0 24 24" aria-label="Email"><path d="M2 5h20v14H2zm2 2v.5l8 5 8-5V7l-8 5z"/></svg></li>
      <li class="web">www.keelstoneautomotive.example.nz
        <svg viewBox="0 0 24 24" aria-label="Website"><path d="M12 2a10 10 0 1 0 0 20 10 10 0 0 0 0-20zm6.9 6h-3a15 15 0 0 0-1.3-3.6A8 8 0 0 1 18.9 8zM12 4a13 13 0 0 1 1.9 4h-3.8A13 13 0 0 1 12 4zM4.3 14a8 8 0 0 1 0-4h3.4a16 16 0 0 0 0 4zm.8 2h3a15 15 0 0 0 1.3 3.6A8 8 0 0 1 5.1 16zm3-8h-3a8 8 0 0 1 4.3-3.6A15 15 0 0 0 8.1 8zM12 20a13 13 0 0 1-1.9-4h3.8A13 13 0 0 1 12 20zm2.3-6H9.7a14 14 0 0 1 0-4h4.6a14 14 0 0 1 0 4zm.3 5.6a15 15 0 0 0 1.3-3.6h3a8 8 0 0 1-4.3 3.6zm1.7-5.6a16 16 0 0 0 0-4h3.4a8 8 0 0 1 0 4z"/></svg></li>
    </ul>
  </section>

</main>
</body>
</html>
```